LunaDorata
Professional
Darlene Oakhurst
Owner
Available for Philadelphia, New Jersey , and New York
LunaDorataPhotography@examplemail.com
Im looking for an elagant design... Luna Dorata means Golden Moon in italian. My co. is after my baby girl (Mila Rose)
I photograph Newborns, Babies, maternity, Children, Family's, Engagements, Pets
Baby Face Big smile
Baby Blue/color edit
Mom with Child
bridge city shot
b&w pic of child with fence
flowers with ring

```html
<!DOCTYPE html>
<html lang="en">
<head>
<meta charset="utf-8">
<title>Luna Dorata Photography – Business Card</title>
<link rel="stylesheet" href="https://fonts.googleapis.com/css2?family=Arimo:wght@400;700&display=swap">
<style>
  :root {
    --page-bg: #e4e4e4;
    --card-top: #3a3a3a;
    --card-mid: #1c1c1c;
    --card-bottom: #0b0b0b;
    --ink: #ffffff;
    --ink-soft: #e6e6e6;
    --accent-blue: #1b8fe0;
    --accent-blue-deep: #0b4f8a;
    --photo-border: #f2f2f2;
  }
  * { box-sizing: border-box; margin: 0; padding: 0; }
  html, body {
    width: 1200px;
    height: 862px;
    overflow: hidden;
    background: var(--page-bg);
    font-family: "Arimo", Arial, sans-serif;
  }
  .business-card {
    position: absolute;
    left: 250px;
    top: 230px;
    width: 700px;
    height: 402px;
    border-radius: 26px;
    background: radial-gradient(ellipse at 50% 20%, var(--card-top) 0%, var(--card-mid) 55%, var(--card-bottom) 100%);
    overflow: hidden;
  }
  .brand-name {
    position: absolute;
    top: 40px;
    left: 0;
    width: 100%;
    text-align: center;
    font-size: 54px;
    font-weight: 400;
    letter-spacing: 1px;
    color: var(--ink);
  }
  .brand-tagline {
    position: absolute;
    top: 110px;
    left: 0;
    width: 100%;
    text-align: center;
    font-size: 17px;
    letter-spacing: 4px;
    color: var(--ink-soft);
    padding-left: 60px;
  }
  .accent-tab {
    position: absolute;
    top: 154px;
    width: 46px;
    height: 108px;
    background: linear-gradient(90deg, var(--accent-blue-deep), var(--accent-blue) 50%, var(--accent-blue-deep));
  }
  .accent-tab--left { left: 0; }
  .accent-tab--right { right: 0; }
  .photo-strip {
    position: absolute;
    top: 130px;
    left: 60px;
    width: 580px;
    height: 156px;
  }
  .photo-frame {
    position: absolute;
    top: 0;
    height: 148px;
    border: 3px solid var(--photo-border);
    box-shadow: 0 4px 10px rgba(0,0,0,0.6);
  }
  .photo-frame--baby-smile {
    left: 2px; width: 196px;
    transform: rotate(-2deg);
    background: linear-gradient(135deg, #d9b9a3, #a8765d 60%, #6d3f30);
  }
  .photo-frame--mother-child {
    left: 200px; width: 184px;
    background: linear-gradient(135deg, #9a9a9a, #4a4a4a 60%, #222);
  }
  .photo-frame--baby-blue {
    left: 386px; width: 192px;
    transform: rotate(2deg);
    background: linear-gradient(135deg, #6f6f6f, #3d3d3d 50%, #2a7fc4 85%, #6cc1f2);
  }
  .contact-block {
    position: absolute;
    top: 290px;
    left: 0;
    width: 100%;
    text-align: center;
    color: var(--ink);
  }
  .contact-name {
    font-size: 21px;
    font-weight: 700;
    margin-bottom: 4px;
  }
  .contact-line {
    font-size: 18px;
    line-height: 25px;
    color: var(--ink-soft);
  }
</style>
</head>
<body>
  <div class="business-card">
    <div class="brand-name">LunaDorata</div>
    <div class="brand-tagline">Photography</div>

    <div class="accent-tab accent-tab--left"></div>
    <div class="accent-tab accent-tab--right"></div>

    <div class="photo-strip">
      <div class="photo-frame photo-frame--baby-smile" role="img" aria-label="Photo of a smiling baby"></div>
      <div class="photo-frame photo-frame--mother-child" role="img" aria-label="Black and white photo of a mother with her child"></div>
      <div class="photo-frame photo-frame--baby-blue" role="img" aria-label="Photo of a baby with a blue color accent"></div>
    </div>

    <div class="contact-block">
      <div class="contact-name">Darlene Oakhurst</div>
      <div class="contact-line">Philadelphia, New Jersey, and New York.</div>
      <div class="contact-line">Phone: 555-014-2738. Cell: 555-019-6620.</div>
      <div class="contact-line">Email: Darlene@LunaDorata.net &nbsp;|&nbsp; www.lunadorata.net</div>
    </div>
  </div>
</body>
</html>
```